Book Cover: Quiet Harbor: Small Ceremonies For The Restless Soul

I would like a full cover spread- front, back and spine as well as a stand alone front cover for Kindle for the book. Design a cover that mirrors the profound depth and dynamic energy of 'Quiet Harbor.' Envision a visual tapestry that draws readers into a transformative journey, where spirituality and self-care unite. Explore vibrant colors, intricate textures, and a sense of inner radiance that beckons readers to explore the book's rich wisdom within. See images for design inspiration attached. Even though some of the images are cartoon, I'd like the cover to be more serious than playful and very elegant.

About this book (back cover copy)
Are you ready to embark on a transformative journey and elevate your daily existence? "Quiet Harbor" is a treasure trove of practical yet profound rituals and wisdom from renowned self-care, healing, and spirituality experts.

Within these pages, you'll uncover a tapestry of guidance and insight from some of the world's most respected mentors. Their collective wisdom is your key to creating a sacred sanctuary within your everyday life.

From invigorating morning rituals to meditative practices, empowering affirmations, and transformative energy healing, you'll find a rich tapestry of tools to nurture a deeper connection with yourself and the universe.

Whether you're a seasoned practitioner or a newcomer to the world of self-care and spirituality, "Quiet Harbor" is your trusted companion on the journey to transform your life and elevate your daily experience. Open this book today and start your sacred, fulfilling adventure.

Colors
0094D4
00A9DD
6FCCEA
C7EBF8
E9F6FB
E54698
E96AAD
F1A4CE
F9D9EA
FCEFF6
6B429C
8869AF
B7A5CE
E3DAEB
F3F0F8

Requirements
Must have
• Title: Quiet Harbor: Subtitle: Small Ceremonies For The Restless Soul Name of Publisher: Lantern Bough Publishing- Logo on the back Back cover copy

```html
<!DOCTYPE html>
<html lang="en">
<head>
<meta charset="utf-8">
<title>Quiet Harbor — Cover Spread</title>
<link rel="stylesheet" href="https://fonts.googleapis.com/css2?family=Great+Vibes&family=Bebas+Neue&family=Arimo:ital,wght@0,400;0,700;1,400&display=swap">
<style>
  :root{
    --stage:#222222;
    --mint:#9fe0bd;
    --mint-deep:#6fcf9f;
    --mist:#f6fbf7;
    --blush:#f1a4ce;
    --rose:#e54698;
    --rose-soft:#e96aad;
    --lilac:#b7a5ce;
    --lilac-pale:#e3daeb;
    --violet:#8869af;
    --gold:#c9a23a;
    --gold-light:#e8c45a;
    --gold-dark:#a27e22;
    --ink:#1d4a37;
    --white:#ffffff;
  }
  *{box-sizing:border-box;margin:0;padding:0}
  html,body{width:1200px;height:1200px;overflow:hidden;background:var(--stage)}
  .spread{
    position:absolute;left:30px;top:195px;width:1140px;height:809px;overflow:hidden;
    background:
      radial-gradient(ellipse 420px 260px at 12% 4%, rgba(111,207,159,.75), transparent 70%),
      radial-gradient(ellipse 520px 300px at 70% 8%, rgba(111,207,159,.8), transparent 70%),
      radial-gradient(ellipse 380px 200px at 35% 30%, rgba(159,224,189,.6), transparent 70%),
      radial-gradient(ellipse 360px 150px at 62% 82%, rgba(229,70,152,.55), transparent 70%),
      radial-gradient(ellipse 480px 180px at 92% 90%, rgba(183,165,206,.7), transparent 70%),
      radial-gradient(ellipse 460px 160px at 20% 100%, rgba(227,218,235,.95), transparent 70%),
      linear-gradient(180deg,#bfeed2 0%,#e7f8ee 35%,var(--mist) 55%,#f6e6f3 78%,#e7d3ef 100%);
  }
  .script{font-family:"Great Vibes",cursive;color:var(--gold);
    background:linear-gradient(160deg,var(--gold-light),var(--gold) 50%,var(--gold-dark));
    -webkit-background-clip:text;background-clip:text;-webkit-text-fill-color:transparent;
    filter:drop-shadow(0 0 6px rgba(255,255,255,.8));font-weight:400;line-height:1;white-space:nowrap}
  .tagline{font-family:"Bebas Neue",sans-serif;color:var(--white);letter-spacing:.5px;
    text-shadow:0 0 6px rgba(80,120,100,.45);white-space:nowrap}
  .tagline .accent{font-family:"Great Vibes",cursive;font-size:1.7em;letter-spacing:0;vertical-align:-.12em;margin-left:4px}

  /* back cover */
  .back{position:absolute;left:0;top:0;width:537px;height:809px}
  .back .title{position:absolute;left:0;width:537px;top:72px;text-align:center;font-size:96px}
  .back .tagline{position:absolute;left:0;width:537px;top:212px;text-align:center;font-size:24px}
  .blurb{position:absolute;left:46px;width:450px;top:258px;font-family:Arimo,sans-serif;
    font-size:13.6px;line-height:21.2px;color:var(--ink);text-align:center}
  .blurb p+p{margin-top:21px}
  .blurb strong{font-weight:700}
  .publisher{position:absolute;left:57px;top:705px;width:170px;text-align:center;
    font-family:Arimo,sans-serif;font-weight:400;font-size:20px;line-height:30px;color:#1a1a1a;letter-spacing:1px}

  /* spine */
  .spine{position:absolute;left:537px;top:0;width:54px;height:809px}
  .spine-text{position:absolute;left:50%;top:22px;transform-origin:0 0;transform:rotate(90deg) translateY(-50%);
    display:flex;align-items:center;gap:18px;white-space:nowrap}
  .spine .title{font-size:50px}
  .spine .tagline{font-size:17px;color:var(--violet);text-shadow:none}
  .spine .imprint{font-family:Arimo,sans-serif;font-size:17px;color:var(--rose);margin-left:22px}

  /* front cover */
  .front{position:absolute;left:591px;top:0;width:549px;height:809px}
  .artwork{position:absolute;left:0;top:18px;width:549px;height:400px;
    background:
      radial-gradient(circle 70px at 68% 30%, rgba(229,70,152,.65), transparent 72%),
      radial-gradient(circle 80px at 90% 50%, rgba(136,105,175,.6), transparent 72%),
      radial-gradient(circle 60px at 24% 28%, rgba(183,120,220,.6), transparent 72%),
      radial-gradient(circle 90px at 28% 58%, rgba(241,164,206,.75), transparent 72%),
      radial-gradient(circle 55px at 52% 22%, rgba(233,106,173,.55), transparent 72%),
      radial-gradient(ellipse 220px 120px at 62% 80%, rgba(255,255,255,.85), transparent 75%);
  }
  .front .title{position:absolute;text-align:left}
  .front .t1{left:40px;top:410px;font-size:165px}
  .front .t2{left:80px;top:570px;font-size:130px}
  .front .tagline{position:absolute;right:40px;top:754px;font-size:26px}
</style>
</head>
<body>
  <main class="spread">
    <section class="back">
      <h2 class="title script">Quiet Harbor</h2>
      <p class="tagline">Small Ceremonies For The Restless<span class="accent">Soul</span></p>
      <div class="blurb">
        <p><strong>Are you ready to embark on a transformative journey and elevate your daily existence?</strong> <em>"Quiet Harbor"</em> is a treasure trove of practical yet profound rituals and wisdom from renowned self-care, healing, and spirituality experts.</p>
        <p>Within these pages, you'll uncover a tapestry of guidance and insight from some of the world's most respected mentors. Their collective wisdom is your key to creating a sacred sanctuary within your everyday life.</p>
        <p>From invigorating morning rituals to meditative practices, empowering affirmations, and transformative energy healing, you'll find a rich tapestry of tools to nurture a deeper connection with yourself and the universe.</p>
        <p>Whether you're a seasoned practitioner or a newcomer to the world of self-care and spirituality, "Quiet Harbor" is your trusted companion on the journey to transform your life and elevate your daily experience. Open this book today and start your sacred, fulfilling adventure.</p>
      </div>
      <p class="publisher">Lantern Bough<br>Publishing</p>
    </section>

    <section class="spine">
      <div class="spine-text">
        <span class="title script">Quiet Harbor</span>
        <span class="tagline">Small Ceremonies For The Restless<span class="accent">Soul</span></span>
        <span class="imprint">Lantern Bough Publishing</span>
      </div>
    </section>

    <section class="front">
      <div class="artwork" role="img" aria-label="Watercolour illustration of pink and violet roses and blossoms with pearls, crowning a serene closed-eyed figure"></div>
      <h1 class="title script t1">Quiet</h1>
      <span class="title script t2">Harbor</span>
      <p class="tagline">Small Ceremonies For The Restless<span class="accent">Soul</span></p>
    </section>
  </main>
</body>
</html>
```